Business Card for Industrial Distributor

We need a business card design for an industrial distributor. We sell machine parts for the manufacturing and oil industry. We would like the cards to look clean and modern but with a touch of industry.

Our colors are blue/white.

Please feel free to visit our website www.korvelpartsco.com

Target Market(s)

mexican manufacturers in the automobile/aerospace industry

Industry/Entity Type

Industrial

Colors
ffffff
0555a3

```html
<!DOCTYPE html>
<html lang="en">
<head>
<meta charset="utf-8">
<title>Korvel Business Card</title>
<link rel="stylesheet" href="https://fonts.googleapis.com/css2?family=Titillium+Web:wght@400;600;700;900&display=swap">
<style>
  :root {
    --canvas-bg: #34302d;
    --brand-blue: #1c3a9c;
    --name-blue: #2f6fc0;
    --ink: #222222;
    --card-white: #ffffff;
    --card-black: #151515;
    --faint-white: #f1f1f1;
    --faint-black: #1c1c1c;
  }
  * { box-sizing: border-box; margin: 0; padding: 0; }
  html, body { width: 1200px; height: 844px; overflow: hidden; }
  body {
    background: var(--canvas-bg);
    font-family: "Titillium Web", Arial, sans-serif;
    position: relative;
  }
  .card {
    position: absolute;
    top: 272px;
    width: 520px;
    height: 300px;
    overflow: hidden;
    box-shadow: 0 10px 24px rgba(0,0,0,0.45);
  }
  .card-front { left: 60px; background: var(--card-white); }
  .card-back { left: 620px; background: var(--card-black); }

  .front-decor {
    position: absolute;
    right: -60px;
    top: -40px;
    width: 250px;
    height: 250px;
    border-radius: 50%;
    background: var(--faint-white);
  }
  .brand-lockup {
    position: absolute;
    left: 34px;
    top: 44px;
    display: flex;
    align-items: center;
    gap: 14px;
  }
  .brand-dot {
    width: 58px;
    height: 58px;
    border-radius: 50%;
    background: var(--brand-blue);
  }
  .brand-name {
    font-weight: 900;
    font-size: 62px;
    line-height: 1;
    color: var(--brand-blue);
    letter-spacing: 0;
    text-transform: uppercase;
  }
  .contact {
    position: absolute;
    left: 40px;
    top: 126px;
    color: var(--ink);
    font-size: 14px;
    line-height: 1.3;
  }
  .person-name { font-size: 20px; color: var(--name-blue); font-weight: 400; line-height: 1.2; }
  .person-role { font-size: 13px; margin-bottom: 10px; }
  .address { margin-bottom: 10px; font-size: 14px; }
  .contact-list { list-style: none; font-size: 14px; }
  .contact-list li { display: flex; align-items: center; gap: 8px; }
  .contact-list svg { width: 11px; height: 11px; fill: var(--name-blue); flex: none; }

  .back-decor {
    position: absolute;
    left: -50px;
    top: -40px;
    width: 260px;
    height: 260px;
    border-radius: 50%;
    background: var(--faint-black);
  }
  .back-brand {
    position: absolute;
    right: 30px;
    top: 144px;
    font-weight: 900;
    font-size: 58px;
    line-height: 1;
    color: var(--card-white);
    text-transform: uppercase;
  }
</style>
</head>
<body>
  <section class="card card-front">
    <div class="front-decor"></div>
    <div class="brand-lockup">
      <div class="brand-dot"></div>
      <div class="brand-name">Korvel</div>
    </div>
    <div class="contact">
      <p class="person-name">Daniel Reyes</p>
      <p class="person-role">Managing Director</p>
      <p class="address">480 Calle Forja Norte<br>Apodaca, N.L. 66600</p>
      <ul class="contact-list">
        <li><svg viewBox="0 0 24 24" aria-hidden="true"><path d="M6.6 10.8a15 15 0 0 0 6.6 6.6l2.2-2.2a1 1 0 0 1 1-.25 11 11 0 0 0 3.6.6 1 1 0 0 1 1 1V20a1 1 0 0 1-1 1A17 17 0 0 1 3 4a1 1 0 0 1 1-1h3.5a1 1 0 0 1 1 1 11 11 0 0 0 .6 3.6 1 1 0 0 1-.25 1z"/></svg>081-442 718 305</li>
        <li><svg viewBox="0 0 24 24" aria-hidden="true"><path d="M2 5h20v14H2z M2 5l10 8 10-8" /></svg>info@korvelpartsco.com</li>
        <li><svg viewBox="0 0 24 24" aria-hidden="true"><path d="M10 14a4 4 0 0 1 0-5.6l3-3a4 4 0 0 1 5.6 5.6l-1.5 1.5-1.4-1.4 1.5-1.5a2 2 0 0 0-2.8-2.8l-3 3a2 2 0 0 0 0 2.8zm4-4a4 4 0 0 1 0 5.6l-3 3a4 4 0 0 1-5.6-5.6l1.5-1.5 1.4 1.4-1.5 1.5a2 2 0 0 0 2.8 2.8l3-3a2 2 0 0 0 0-2.8z"/></svg>www.korvelpartsco.com</li>
      </ul>
    </div>
  </section>

  <section class="card card-back">
    <div class="back-decor"></div>
    <div class="back-brand">Korvel</div>
  </section>
</body>
</html>
```